Business Card for a Dental Office

The design should communicate integrity, quality and reliability. We also want the card look elegant, simple, but still stand out, different from the traditional-dental-office business card.

Industry/Entity Type

Business

```html
<!DOCTYPE html>
<html lang="en">
<head>
<meta charset="utf-8">
<title>Harlow Dental Centre – Business Card</title>
<link href="https://fonts.googleapis.com/css2?family=Open+Sans:wght@400;600;700&display=swap" rel="stylesheet">
<style>
  :root {
    --backdrop: #5b3d2a;
    --card: #ffffff;
    --ink: #111111;
    --gold: #c9a21a;
    --gold-light: #f2e21e;
    --gold-dark: #9c7a12;
    --rule: #222222;
  }
  * { margin: 0; padding: 0; box-sizing: border-box; }
  html, body { width: 1200px; height: 1000px; overflow: hidden; }
  body {
    background: var(--backdrop);
    font-family: "Open Sans", Arial, sans-serif;
    color: var(--ink);
    position: relative;
  }
  .card {
    position: absolute;
    left: 265px;
    width: 665px;
    background: var(--card);
    overflow: hidden;
    box-shadow: 0 6px 14px rgba(0,0,0,0.45);
  }
  .card--front { top: 73px; height: 397px; }
  .card--back { top: 532px; height: 398px; }

  .brand { position: absolute; display: flex; align-items: center; gap: 14px; }
  .brand__mark { background: var(--ink); flex: none; }
  .brand__text { display: flex; flex-direction: column; }
  .brand__name {
    font-weight: 700; color: var(--ink); text-transform: uppercase;
    letter-spacing: 0.5px; line-height: 1; white-space: nowrap;
  }
  .brand__tagline {
    font-weight: 600; color: var(--gold); text-transform: uppercase;
    letter-spacing: 0.8px; line-height: 1; margin-top: 6px; white-space: nowrap;
  }
  .card--front .brand { left: 115px; top: 56px; }
  .card--front .brand__mark { width: 96px; height: 96px; }
  .card--front .brand__name { font-size: 29px; }
  .card--front .brand__tagline { font-size: 14.5px; }
  .card--back .brand { left: 97px; top: 128px; }
  .card--back .brand__mark { width: 104px; height: 104px; }
  .card--back .brand__name { font-size: 31px; }
  .card--back .brand__tagline { font-size: 15.5px; }

  .doctors {
    position: absolute; left: 63px; top: 208px; list-style: none;
  }
  .doctors li { font-size: 17px; font-weight: 700; line-height: 33.5px; white-space: nowrap; }
  .doctors .degree { font-size: 14px; font-weight: 400; }

  .divider {
    position: absolute; left: 332px; top: 212px; width: 2px; height: 120px;
    background: var(--rule);
  }

  .contact { position: absolute; left: 354px; top: 208px; font-size: 15px; line-height: 20px; }
  .contact p { white-space: nowrap; }
  .contact .address { margin-bottom: 4px; }
  .contact .row { display: flex; align-items: center; gap: 8px; }
  .contact .row svg { width: 16px; height: 14px; flex: none; }

  .band {
    position: absolute; left: 0; right: 0; bottom: 0; height: 32px;
    background: linear-gradient(90deg, var(--ink) 0%, var(--ink) 45.5%, var(--gold-dark) 45.6%, var(--gold) 60%, var(--gold-light) 100%);
  }
  .band__mark {
    position: absolute; left: 318px; top: 6px; width: 20px; height: 20px; background: #ffffff;
  }
</style>
</head>
<body>
  <section class="card card--front" aria-label="Card front">
    <div class="brand">
      <div class="brand__mark"></div>
      <div class="brand__text">
        <span class="brand__name">Harlow Dental Centre</span>
        <span class="brand__tagline">Quality care for every family smile</span>
      </div>
    </div>

    <ul class="doctors">
      <li>Dr. Martin L. Osgood, <span class="degree">DMD</span></li>
      <li>Dr. Peter R. Haldane, <span class="degree">DMD</span></li>
      <li>Dr. Clara J. Wendt, <span class="degree">DMD</span></li>
      <li>Dr. Minh Q. Pham, <span class="degree">DDS</span></li>
    </ul>

    <div class="divider"></div>

    <div class="contact">
      <p class="address">418 Alder Crescent, Harlow,<br>MB R5K 2T4</p>
      <p>Toll Free 1 (888) 555 0147</p>
      <p class="row">
        <svg viewBox="0 0 16 14" aria-hidden="true"><path fill="#c9a21a" d="M1 4c0-2 2-3 7-3s7 1 7 3v1h-4V3.5H5V5H1zM3 6h10l2 7H1z"/><circle cx="8" cy="9.5" r="2" fill="#fff"/></svg>
        1 (204) 555 0182
      </p>
      <p class="row">
        <svg viewBox="0 0 16 14" aria-hidden="true"><path fill="#c9a21a" d="M4 0h8v4H4zM1 5h14v6h-3V9H4v2H1zM4 10h8v4H4z"/></svg>
        1 (204) 555 0193
      </p>
      <p class="row">
        <svg viewBox="0 0 16 14" aria-hidden="true"><rect x="1" y="2" width="14" height="10" fill="#c9a21a"/><path d="M1 2l7 6 7-6" fill="none" stroke="#fff" stroke-width="1.2"/></svg>
        harlowdental@examplemail.net
      </p>
    </div>

    <div class="band"><div class="band__mark"></div></div>
  </section>

  <section class="card card--back" aria-label="Card back">
    <div class="brand">
      <div class="brand__mark"></div>
      <div class="brand__text">
        <span class="brand__name">Harlow Dental Centre</span>
        <span class="brand__tagline">Quality care for every family smile</span>
      </div>
    </div>
  </section>
</body>
</html>
```